Custom unique Stationary design for Logistics company

We need a custom, unique , elegant and luxurious full stationary design using our new logo, following these guidelines:
1- Business card: double sided, both sides uses the navy blue as the background main color (same as the code of the navy blue used in our logo).
2- envelope and folder: also use the same navy blue as the main background color.
3- book cover( notepad cover) : same thing with the navy blue
4- letterhead: feel free to use the combination of the colors in our logo.
5- rest of the items are up to your creativity

Target Market(s)

corporates and other businesses

Industry/Entity Type

Logistics and heavy machines contractors

Requirements
Must have
• Letterhead, business card, envelope, notepad cover, paper, file
Nice to have
• navy blue to be main background color for business card, envelope, notepad cover

```html
<!DOCTYPE html>
<html lang="en">
<head>
<meta charset="utf-8">
<title>Northvale Cargo Letterhead</title>
<link href="https://fonts.googleapis.com/css2?family=Lato:wght@400;700;900&family=Satisfy&display=swap" rel="stylesheet">
<style>
  :root {
    --navy: #0f4a73;
    --navy-deep: #0b3f63;
    --orange: #e8572a;
    --ink: #2f3337;
    --muted: #55595d;
    --paper: #ffffff;
    --backdrop: #e6e7e9;
  }
  * { box-sizing: border-box; margin: 0; padding: 0; }
  html, body {
    width: 1200px; height: 960px; overflow: hidden;
    background: var(--backdrop);
    font-family: "Lato", sans-serif;
    color: var(--ink);
  }
  .letterhead {
    position: absolute; left: 280px; top: 27px;
    width: 640px; height: 906px;
    background: var(--paper);
    overflow: hidden;
  }
  .brand {
    position: absolute; left: 52px; top: 62px;
    display: flex; align-items: center; gap: 10px;
  }
  .brand-dot { width: 14px; height: 14px; border-radius: 50%; background: var(--orange); }
  .brand-name {
    font-weight: 900; font-size: 27px; color: var(--navy); letter-spacing: 0.5px;
  }
  .contact {
    position: absolute; right: 48px; top: 40px;
    font-size: 9.5px; line-height: 13px; color: var(--ink);
  }
  .contact-address { margin-bottom: 5px; }
  .contact-row { display: flex; align-items: center; gap: 5px; padding-left: 14px; }
  .contact-row svg { width: 8px; height: 8px; flex: none; }
  .header-rule {
    position: absolute; left: 52px; right: 48px; top: 132px;
    height: 1.5px; background: var(--navy);
  }
  .letter {
    position: absolute; left: 92px; top: 168px; width: 470px;
    font-size: 10px; line-height: 13px; color: var(--ink);
  }
  .letter-date { font-size: 11px; margin-bottom: 16px; }
  .recipient { margin-bottom: 14px; font-size: 10.5px; }
  .recipient p + p { margin-top: 12px; }
  .salutation { font-weight: 700; font-size: 13px; margin-bottom: 10px; }
  .body-copy p { margin-bottom: 14px; }
  .closing { margin-top: 6px; font-size: 10.5px; }
  .signature {
    font-family: "Satisfy", cursive; font-size: 34px; color: var(--ink);
    margin-top: 10px; margin-left: 40px;
  }
  .footer-wave { position: absolute; left: 0; bottom: 0; width: 640px; height: 906px; }
</style>
</head>
<body>
  <main class="letterhead">
    <div class="brand">
      <span class="brand-dot"></span>
      <span class="brand-name">Northvale Cargo</span>
    </div>

    <address class="contact" style="font-style:normal">
      <div class="contact-address">Harbor Point 2100 Quay Road<br>Suite 310</div>
      <div class="contact-row">
        <svg viewBox="0 0 10 10"><path d="M2 1h2l1 2.5-1.3 1a5 5 0 0 0 2 2l1-1.3L9 6v2a1 1 0 0 1-1 1A7 7 0 0 1 1 2a1 1 0 0 1 1-1z" fill="var(--navy)"/></svg>
        020 418 7732
      </div>
      <div class="contact-row">
        <svg viewBox="0 0 10 10"><rect x="0.5" y="2" width="9" height="6" fill="var(--navy)"/><path d="M0.5 2l4.5 3.5L9.5 2" stroke="#fff" stroke-width="0.8" fill="none"/></svg>
        hello@northvalecargo.com
      </div>
      <div class="contact-row">
        <svg viewBox="0 0 10 10"><circle cx="5" cy="5" r="4.5" fill="var(--navy)"/><path d="M0.5 5h9M5 0.5c-2.4 2.5-2.4 6.5 0 9M5 0.5c2.4 2.5 2.4 6.5 0 9" stroke="#fff" stroke-width="0.6" fill="none"/></svg>
        www.northvalecargo.com
      </div>
    </address>

    <div class="header-rule"></div>

    <article class="letter">
      <p class="letter-date">January-03-2020</p>
      <div class="recipient">
        <p>Mr, Peter Lane<br>President</p>
        <p>Ridge Industries<br>48 Mill Avenue, Suite# 12<br>Eastford, State, 340017</p>
      </div>
      <p class="salutation">Dear Mr, Peter</p>
      <div class="body-copy">
        <p>Lorem ipsum dolor sit amet, consectetur adipisicing elit, sed do eiusmod tempor incididunt ut labore et dolore magna aliqua. Ut enim ad minim veniam, quis nostrud exercitation ullamco laboris nisi ut aliquip ex ea commodo consequat. Duis aute irure dolor in reprehenderit in voluptate velit esse cillum dolore eu fugiat nulla pariatur.</p>
        <p>Lorem ipsum dolor sit amet, consectetur adipisicing elit, sed do eiusmod tempor incididunt ut labore et dolore magna aliqua. Ut enim ad minim veniam, quis nostrud exercitation ullamco laboris nisi ut aliquip ex ea commodo consequat. Duis aute irure dolor in reprehenderit in voluptate velit esse cillum dolore eu fugiat nulla pariatur.</p>
        <p>Lorem ipsum dolor sit amet, consectetur adipisicing elit, sed do eiusmod tempor incididunt ut labore et dolore magna aliqua. Ut enim ad minim veniam, quis nostrud exercitation ullamco laboris nisi ut aliquip ex ea commodo consequat.</p>
        <p>Excepteur sint occaecat cupidatat non proident, sunt in culpa qui officia deserunt mollit anim id est laborum. re et dolore magnam aliquam quaerat voluptatem.</p>
      </div>
      <p class="closing">Regards</p>
      <p class="signature">Daniel Reyes</p>
    </article>

    <svg class="footer-wave" viewBox="0 0 640 906" aria-hidden="true">
      <path d="M0 906 Q 520 880 640 768 L640 906 Z" fill="var(--navy-deep)"/>
      <path d="M22 893 Q 520 858 624 792 Q 545 868 22 893 Z" fill="var(--orange)"/>
    </svg>
  </main>
</body>
</html>
```